Quiet Harbor Prints gallery website

I need a Website for a gallery with a shopify integration or maybe even better also compatible with squarespace.
the website should have following riders: Künstler, Veranstaltungen, Shop, About Us.
some nice examples for inspiration of the website architecture are:
https://www.lindwerkraum.com/
https://www.plattenbau-salon.com/de/
https://moorlichtraum.de/
It should be easy for us to make adaptations and fill the website with new content.
Attached there is the CI an logo for the brand.
Target Market(s)
Art Collectors,
Industry/Entity Type
artgallery
Coding
Coded - Design and coding required
Number of Pages Required
3 page
Font styles to use
Look and feel

```html
<!DOCTYPE html>
<html lang="en">
<head>
<meta charset="utf-8">
<title>Quiet Harbor Prints</title>
<link href="https://fonts.googleapis.com/css2?family=Open+Sans:wght@400;600;700;800&family=Montserrat:wght@400;500;600;700&display=swap" rel="stylesheet">
<style>
:root{
  --red:#b3232b;
  --red-dark:#8f1a20;
  --ink:#1f1f1f;
  --text:#555;
  --pink:#f7e7e7;
  --white:#fff;
  --line:#d8d8d8;
  --star:#f2b01e;
}
*{box-sizing:border-box;margin:0;padding:0}
html,body{width:1200px;height:3724px;overflow:hidden}
body{font-family:"Montserrat",sans-serif;color:var(--ink);background:var(--white);position:relative}
h1,h2,h3{font-family:"Open Sans",sans-serif}
.btn{display:inline-block;background:var(--red);color:var(--white);font:600 15px "Montserrat",sans-serif;padding:14px 44px;border-radius:2px}

/* hero */
.hero{position:absolute;left:0;top:0;width:1200px;height:640px;overflow:hidden}
.hero-photo{position:absolute;inset:0;background:linear-gradient(100deg,#2b2320 0%,#4a3a33 35%,#7a6a66 60%,#5b6f88 80%,#3a3540 100%)}
.hero-shade{position:absolute;inset:0;background:linear-gradient(90deg,rgba(0,0,0,.55),rgba(0,0,0,.15))}
.brand{position:absolute;left:112px;top:44px;display:flex;align-items:center;gap:14px;color:var(--white);font:700 22px "Open Sans",sans-serif;letter-spacing:1px}
.brand-mark{width:26px;height:26px;background:var(--red)}
.nav{position:absolute;top:32px;left:636px;display:flex;gap:58px}
.nav a{color:var(--white);font:700 15px "Montserrat",sans-serif;text-decoration:none}
.hero-copy{position:absolute;left:112px;top:200px}
.hero-copy .welcome{color:var(--white);font:800 30px "Open Sans",sans-serif}
.hero-copy .title{font:800 68px/1.05 "Open Sans",sans-serif;margin-top:10px}
.hero-copy .title .accent{color:var(--red);display:block}
.hero-copy .title .plain{color:var(--white);display:block}
.hero-copy .btn{margin-top:26px}
.edge{position:absolute;left:0;width:1200px}

/* about */
.about{position:absolute;left:0;top:700px;width:1200px;height:420px}
.about-block{position:absolute;left:112px;top:28px;width:150px;height:60px;background:var(--red)}
.about-photo{position:absolute;left:140px;top:60px;width:412px;height:300px;background:linear-gradient(135deg,#b7a48d,#6b5548 45%,#c9b28a 70%,#8a6a52)}
.about-copy{position:absolute;left:600px;top:26px;width:390px}
.about-copy h2{color:var(--red);font-size:40px;font-weight:800}
.about-copy p{font-size:15px;line-height:1.55;color:var(--text);margin-top:10px}
.about-copy .btn{margin-top:24px}

/* events */
.events{position:absolute;left:0;top:1168px;width:1200px;height:830px;background:var(--pink)}
.section-title{text-align:center;color:var(--red);font:800 38px "Open Sans",sans-serif}
.events .section-title{position:absolute;top:52px;width:100%}
.event-grid{position:absolute;left:112px;top:132px;width:976px;display:grid;grid-template-columns:repeat(3,1fr);grid-template-rows:292px 296px}
.event{position:relative;overflow:hidden;border:1px solid rgba(255,255,255,.4)}
.event-date{position:absolute;right:0;top:8px;width:76px;background:var(--red);color:var(--white);text-align:center;font:800 26px/1 "Open Sans",sans-serif;padding:8px 0}
.event-date span{display:block;font-size:34px;margin-top:4px}
.event-name{position:absolute;bottom:26px;width:100%;text-align:center;color:var(--white);font:700 22px "Open Sans",sans-serif}
.event-feature{background:#3b2a2c;border:4px solid var(--red-dark);color:var(--white);text-align:center;padding:56px 40px 0}
.event-feature h3{font-size:24px;font-weight:700}
.event-feature .when{font-size:18px;margin-top:8px;font-weight:600}
.event-feature p{font-size:14px;line-height:1.5;margin-top:12px}
.events .btn{position:absolute;left:504px;top:760px;padding:12px 52px}

/* artists */
.artists{position:absolute;left:0;top:2060px;width:1200px;height:660px}
.artists .section-title{margin-top:44px}
.artist-row{position:absolute;top:124px;left:108px;display:flex;gap:48px}
.artist{width:296px;height:424px;background:var(--white);box-shadow:0 2px 12px rgba(0,0,0,.15);text-align:center;padding-top:28px}
.artist-photo{width:196px;height:196px;border-radius:50%;margin:0 auto;background:linear-gradient(180deg,#cfd4da,#7d8793 60%,#2d3440)}
.artist h3{font-size:20px;margin-top:22px}
.artist .role{font-size:14px;color:var(--text);margin-top:2px}
.artist p{font-size:14px;color:var(--text);line-height:1.5;margin:14px 22px 0}
.artist .social{width:30px;height:30px;border-radius:50%;border:2px solid #444;margin:18px auto 0}
.dots{position:absolute;top:594px;left:568px;display:flex;gap:14px;align-items:center}
.dots span{width:10px;height:10px;border-radius:50%;background:var(--red)}
.dots .on{width:20px;height:20px;border:3px solid var(--red);background:var(--white);box-shadow:inset 0 0 0 3px var(--white),inset 0 0 0 10px var(--red)}

/* shop */
.shop{position:absolute;left:0;top:2752px;width:1200px;height:708px;background:var(--red)}
.shop .section-title{color:var(--white);position:absolute;top:72px;width:100%}
.shop-card{position:absolute;background:var(--white);text-align:center;overflow:hidden}
.shop-card .art{height:218px}
.shop-card h3{font-size:24px;margin-top:22px}
.shop-card p{font-size:14px;color:var(--text);line-height:1.5;margin:10px 30px 0}
.stars{margin-top:12px;font-size:20px;color:var(--star)}
.stars small{font-size:13px;color:var(--text)}
.shop-card.featured{color:var(--white);border:6px solid var(--white);box-shadow:0 6px 20px rgba(0,0,0,.35)}
.shop-card.featured .art{position:absolute;inset:0;height:auto}
.shop-card.featured .body{position:absolute;left:0;right:0;top:250px}
.shop-card.featured p{color:var(--white)}
.shop-card.featured .stars small{color:var(--white)}
.price{font:800 28px "Open Sans",sans-serif;margin-top:8px}
.arrow{position:absolute;top:3120px;width:44px;height:44px;border-radius:50%;background:var(--white)}

/* footer */
.footer{position:absolute;left:0;top:3480px;width:1200px;height:244px}
.footer-nav{position:absolute;top:50px;left:0;width:100%;display:flex;justify-content:center;gap:30px;font:600 15px "Montserrat",sans-serif}
.footer-nav .sep{color:#888}
.footer-rule{position:absolute;left:100px;right:100px;top:92px;border-top:1px solid var(--line)}
.footer-social{position:absolute;left:112px;top:126px;display:flex;gap:28px}
.footer-social span{width:36px;height:36px;border-radius:50%;background:var(--red)}
.footer-col{position:absolute;top:120px;display:flex;gap:10px;font-size:14px;color:var(--text);line-height:1.6}
.footer-col svg{flex:none;margin-top:3px}
</style>
</head>
<body>

<header class="hero">
  <div class="hero-photo" role="img" aria-label="Artist painting a large canvas in the studio"></div>
  <div class="hero-shade"></div>
  <div class="brand"><span class="brand-mark"></span>QUIET HARBOR PRINTS</div>
  <nav class="nav"><a>ARTISTS</a><a>EVENTS</a><a>SHOP</a><a>ABOUT US</a></nav>
  <div class="hero-copy">
    <div class="welcome">WELCOME TO</div>
    <h1 class="title"><span class="accent">QUIET HARBOR</span><span class="plain">PRINTS</span></h1>
    <a class="btn">Get Started</a>
  </div>
  <svg class="edge" style="top:600px" width="1200" height="40" viewBox="0 0 1200 40" preserveAspectRatio="none"><path d="M0 22 L60 16 L120 24 L200 14 L280 22 L360 12 L440 20 L520 14 L600 24 L680 14 L760 22 L840 12 L920 20 L1000 14 L1080 22 L1140 16 L1200 20 V40 H0Z" fill="#fff"/></svg>
</header>

<section class="about">
  <div class="about-block"></div>
  <div class="about-photo" role="img" aria-label="Painter working on a canvas at an easel"></div>
  <div class="about-copy">
    <h2>ABOUT US</h2>
    <p>Lorem Ipsum is simply dummy text of the printing and typesetting industry. Lorem Ipsum has been the industry's standard dummy text ever since the 1500s, when an unknown printer took a galley of type and scrambled it to make a type specimen book. It has survived not only five centuries, but also the leap into electronic typesetting, remaining essentially unchanged.Lorem Ipsum is simply dummy text of the</p>
    <a class="btn">Get Started</a>
  </div>
</section>

<section class="events">
  <svg class="edge" style="top:-14px" width="1200" height="30" viewBox="0 0 1200 30" preserveAspectRatio="none"><path d="M0 14 L80 8 L160 16 L240 6 L320 14 L400 8 L480 16 L560 6 L640 14 L720 8 L800 16 L880 6 L960 14 L1040 8 L1120 16 L1200 10 V30 H0Z" fill="#f7e7e7"/></svg>
  <h2 class="section-title">OUR EVENTS</h2>
  <div class="event-grid">
    <div class="event" role="img" aria-label="Painting of white flowers on blue" style="background:linear-gradient(150deg,#2f5fa8,#9cc3e8 45%,#f3f1ea 60%,#3a6fb8)"><div class="event-date">MAR<span>15</span></div><div class="event-name">Lorem Ipsum</div></div>
    <div class="event" role="img" aria-label="Painting with soft red and cream brushstrokes" style="background:linear-gradient(150deg,#e9ddd2,#c68a7a 45%,#b23a35 70%,#efe4da)"><div class="event-date">MAR<span>21</span></div><div class="event-name">Lorem Ipsum</div></div>
    <div class="event" role="img" aria-label="Colourful abstract flower painting" style="background:linear-gradient(150deg,#e64b7a,#f3b23a 35%,#4bb0d8 65%,#7a3fa0)"><div class="event-date">MAR<span>23</span></div><div class="event-name">Lorem Ipsum</div></div>
    <div class="event" role="img" aria-label="Vivid close-up painting in blue, amber and magenta" style="background:linear-gradient(160deg,#2f6f9a,#3a5a8a 45%,#8a4a7a 75%,#b2556a)"><div class="event-date">MAR<span>25</span></div><div class="event-name">Lorem Ipsum</div></div>
    <div class="event event-feature">
      <h3>Lorem Ipsum</h3>
      <div class="when">Mar, 27 2024</div>
      <p>Lorem Ipsum is simply dummy text of the printing and typesetting industry. Lorem Ipsum has been the</p>
    </div>
    <div class="event" role="img" aria-label="Abstract painting in purple, orange and teal" style="background:linear-gradient(160deg,#5a2f7a,#e0603a 40%,#f0c070 55%,#2a8a9a 80%)"><div class="event-date">MAR<span>28</span></div><div class="event-name">Lorem Ipsum</div></div>
  </div>
  <a class="btn">View All</a>
</section>

<section class="artists">
  <h2 class="section-title">OUR ARTISTS</h2>
  <div class="artist-row">
    <div class="artist"><div class="artist-photo" role="img" aria-label="Portrait of Alex"></div><h3>Alex</h3><div class="role">Artists</div><p>Lorem Ipsum is simply dummy text of the printing and typesetting industry.</p><div class="social"></div></div>
    <div class="artist"><div class="artist-photo" role="img" aria-label="Portrait of John"></div><h3>John</h3><div class="role">Artists</div><p>Lorem Ipsum is simply dummy text of the printing and typesetting industry.</p><div class="social"></div></div>
    <div class="artist"><div class="artist-photo" role="img" aria-label="Portrait of Robin"></div><h3>Robin</h3><div class="role">Artists</div><p>Lorem Ipsum is simply dummy text of the printing and typesetting industry.</p><div class="social"></div></div>
  </div>
  <div class="dots"><span class="on"></span><span></span><span></span></div>
</section>

<section class="shop">
  <svg class="edge" style="top:-14px" width="1200" height="30" viewBox="0 0 1200 30" preserveAspectRatio="none"><path d="M0 12 L70 6 L150 16 L230 6 L310 14 L390 6 L470 16 L550 8 L630 14 L710 6 L790 16 L870 8 L950 14 L1030 6 L1110 14 L1200 8 V30 H0Z" fill="#b3232b"/></svg>
  <h2 class="section-title">OUR SHOP</h2>
  <div class="shop-card" style="left:112px;top:158px;width:308px;height:430px">
    <div class="art" role="img" aria-label="Painting of a stag in an autumn landscape" style="background:linear-gradient(180deg,#d9c9a8,#b89466 55%,#6a5a3a)"></div>
    <h3>Lorem Ipsum</h3><p>Lorem Ipsum is simply dummy text of the printing and typesetting industry.</p>
    <div class="stars">★★★★★ <small>(125)</small></div>
  </div>
  <div class="shop-card featured" style="left:440px;top:142px;width:320px;height:468px">
    <div class="art" role="img" aria-label="Abstract painting in rust and deep teal" style="background:linear-gradient(170deg,#b8562a,#6a3a22 40%,#1f3a40 75%,#102428)"></div>
    <div class="body">
      <h3>Lorem Ipsum</h3><p>Lorem Ipsum is simply dummy text of the printing and typesetting industry.</p>
      <div class="stars">★★★★★ <small>(125)</small></div>
      <div class="price">$1000</div>
    </div>
  </div>
  <div class="shop-card" style="left:780px;top:158px;width:308px;height:430px">
    <div class="art" role="img" aria-label="Painting of a harbour town at dusk" style="background:linear-gradient(180deg,#3a5a78,#c07a3a 55%,#1f3a55)"></div>
    <h3>Lorem Ipsum</h3><p>Lorem Ipsum is simply dummy text of the printing and typesetting industry.</p>
    <div class="stars">★★★★★ <small>(125)</small></div>
  </div>
  <svg class="edge" style="top:690px" width="1200" height="30" viewBox="0 0 1200 30" preserveAspectRatio="none"><path d="M0 0 H1200 V14 L1120 22 L1040 12 L960 20 L880 10 L800 20 L720 12 L640 22 L560 12 L480 20 L400 10 L320 20 L240 12 L160 22 L80 12 L0 18Z" fill="#b3232b"/></svg>
</section>
<svg class="arrow" style="left:32px" viewBox="0 0 44 44"><circle cx="22" cy="22" r="22" fill="#fff"/><path d="M25 14 L17 22 L25 30" stroke="#b3232b" stroke-width="3" fill="none"/></svg>
<svg class="arrow" style="left:1124px" viewBox="0 0 44 44"><circle cx="22" cy="22" r="22" fill="#fff"/><path d="M19 14 L27 22 L19 30" stroke="#b3232b" stroke-width="3" fill="none"/></svg>

<footer class="footer">
  <nav class="footer-nav"><a>ARTISTS</a><span class="sep">|</span><a>EVENTS</a><span class="sep">|</span><a>SHOP</a><span class="sep">|</span><a>ABOUT US</a></nav>
  <div class="footer-rule"></div>
  <div class="footer-social"><span></span><span></span></div>
  <div class="footer-col" style="left:380px">
    <svg width="14" height="18" viewBox="0 0 14 18"><path d="M7 0a7 7 0 0 0-7 7c0 5 7 11 7 11s7-6 7-11a7 7 0 0 0-7-7z" fill="#b3232b"/><circle cx="7" cy="7" r="2.5" fill="#fff"/></svg>
    <div>Hafenweg 12<br>20457 Harborside</div>
  </div>
  <div class="footer-col" style="left:636px">
    <svg width="16" height="18" viewBox="0 0 16 18"><rect x="0" y="3" width="16" height="12" fill="#b3232b"/><path d="M0 3 L8 10 L16 3" stroke="#fff" fill="none"/></svg>
    <div>hello@quietharbor.art<br>0170 555 01 23</div>
  </div>
  <div class="footer-col" style="left:888px;width:200px">
    <svg width="16" height="16" viewBox="0 0 16 16"><circle cx="8" cy="8" r="8" fill="#b3232b"/></svg>
    <div>© 2024 Quiet Harbor Prints All Rights Reserved</div>
  </div>
</footer>

</body>
</html>
```